Custom Cabinet Shop Needs a website design

Hi,
We need a website for a Custom Cabinet Shop and Cabinet parts manufacturing business.
The business has two sides to it. One side provides custom Kitchens, vanities, entertainment units, offices and what not to homeowners and contractors.
The 2nd side of the business provides built to order cabinet boxes and other parts required to put together a project to other cabinet shops, small contractors looking to install there own cabinets.
Website will need a Gallery to display work.
Color scheme to go well with logo.
current website is www.brambleoakcustomcabinets.com
being changed to www.brambleoak.ca
Logo Included in attached files.
Tagline "Joinery with Spirit"
Mission Statement "Our passion is to deliver inspired cabinetry solutions to suit all your needs, supported by our phenomenal star class customer service"
The website should convey quality and professionalism.
Thank you.
Homeowners/ Contractors
Entertainment

```html
<!DOCTYPE html>
<html lang="en">
<head>
<meta charset="utf-8">
<title>Bramble Oak Custom Cabinets</title>
<link href="https://fonts.googleapis.com/css2?family=Open+Sans:wght@400;600;700&display=swap" rel="stylesheet">
<style>
  :root{
    --black:#000;
    --ink:#111;
    --text:#555;
    --accent:#e8451f;
    --footer:#232323;
    --footer-text:#bbb;
    --white:#fff;
  }
  *{margin:0;padding:0;box-sizing:border-box}
  html,body{width:774px;height:1200px;overflow:hidden;background:var(--white)}
  body{position:relative;font-family:"Open Sans",sans-serif;color:var(--ink)}
  .abs{position:absolute}
  .site-header{left:0;top:0;width:774px;height:54px;background:var(--black)}
  .brand{left:64px;top:15px;display:flex;align-items:center;gap:6px;color:var(--white);font-weight:700;font-size:15px;letter-spacing:.5px;text-transform:uppercase}
  .brand-dot{width:12px;height:12px;border-radius:50%;background:var(--accent)}
  .main-nav{top:22px;left:0;width:774px;height:12px}
  .main-nav a{position:absolute;transform:translateX(-50%);color:#ddd;font-size:7px;font-weight:600;text-decoration:none;letter-spacing:.2px}
  .hero{left:0;top:54px;width:774px;height:346px;background:linear-gradient(160deg,#2c3240 0%,#232833 45%,#3a342e 75%,#2a2620 100%)}
  .hero-title{left:0;top:186px;width:774px;text-align:center;color:var(--white);font-size:20px;font-weight:700;letter-spacing:.3px;text-transform:uppercase}
  .hero-text{left:110px;top:219px;width:554px;text-align:center;color:#eee;font-size:12px;line-height:21px}
  .btn-outline{left:328px;top:277px;width:118px;height:27px;border:1.5px solid var(--white);color:var(--white);font-size:7px;font-weight:700;display:flex;align-items:center;justify-content:center;text-transform:uppercase}
  .hero-next{left:721px;top:201px}
  .section-title{left:0;width:774px;text-align:center;font-size:13px;font-weight:700;text-transform:uppercase}
  .rule{left:327px;width:120px;height:1.5px;background:var(--accent)}
  .intro{left:0;top:483px;width:774px;text-align:center;font-size:7px;color:var(--text);text-transform:uppercase}
  .tile{width:189px;height:111px}
  .caption{width:189px;text-align:center;font-size:6.5px;line-height:12.5px;color:var(--ink);text-transform:uppercase}
  .about{left:100px;top:910px;width:574px;text-align:center;font-size:9px;line-height:17.6px;color:var(--text)}
  .btn-solid{left:310px;top:983px;width:154px;height:30px;background:var(--accent);color:var(--white);font-size:7.5px;font-weight:700;display:flex;align-items:center;justify-content:center;text-transform:uppercase}
  .site-footer{left:0;top:1054px;width:774px;height:146px;background:var(--footer)}
  .footer-nav{left:0;top:1083px;width:774px;text-align:center;font-size:6.5px;color:var(--footer-text);text-transform:uppercase;word-spacing:2px}
  .footer-nav span{margin:0 12px}
  .copyright{left:0;top:1104px;width:774px;text-align:center;font-size:6px;color:#999;text-transform:uppercase}
  .social{left:344px;top:1123px;display:flex;gap:4.5px}
  .social i{display:block;width:13px;height:13px;border-radius:50%;background:#777}
  .footer-brand{left:0;top:1156px;width:774px;display:flex;justify-content:center;align-items:center;gap:5px;color:var(--white);font-weight:700;font-size:12px;text-transform:uppercase}
  .footer-brand .brand-dot{width:10px;height:10px}
</style>
</head>
<body>
  <header class="abs site-header"></header>
  <div class="abs brand"><span class="brand-dot"></span>Bramble Oak</div>
  <nav class="abs main-nav">
    <a style="left:392px">HOME</a>
    <a style="left:461px">GALLERY</a>
    <a style="left:535px">SERVICES</a>
    <a style="left:614px">WARRANTY</a>
    <a style="left:693px">CONTACT</a>
  </nav>

  <section class="abs hero" role="img" aria-label="Dim kitchen interior with a bar counter, stools and pendant lights"></section>
  <h1 class="abs hero-title">Joinery with Spirit</h1>
  <p class="abs hero-text">Our passion is to deliver inspired cabinetry solutions to suit all your needs, supported by our phenomenal star class customer service</p>
  <div class="abs btn-outline">Click here for details</div>
  <svg class="abs hero-next" width="24" height="24" viewBox="0 0 24 24"><circle cx="12" cy="12" r="11" fill="rgba(255,255,255,.12)"/><path d="M10 7l5 5-5 5" fill="none" stroke="rgba(255,255,255,.35)" stroke-width="2"/></svg>

  <h2 class="abs section-title" style="top:437px">Welcome to Bramble Oak</h2>
  <div class="abs rule" style="top:464px"></div>
  <p class="abs intro">Our passion is to deliver inspired cabinetry solutions to suit all your needs, supported by our phenomenal star class customer service</p>

  <div class="abs tile" style="left:0;top:524px;background:linear-gradient(180deg,#d9d6cf,#6d5444)" role="img" aria-label="White kitchen with dark island"></div>
  <div class="abs tile" style="left:195px;top:524px;background:linear-gradient(180deg,#b9b0a3,#5a3826)" role="img" aria-label="Kitchen island with wine rack and hardwood floor"></div>
  <div class="abs tile" style="left:390px;top:524px;background:linear-gradient(180deg,#8f8676,#2b2622)" role="img" aria-label="Bathroom vanity beside a soaker tub"></div>
  <div class="abs tile" style="left:585px;top:524px;background:linear-gradient(180deg,#c8c2b6,#3d3630)" role="img" aria-label="Kitchen with bar seating and stainless appliances"></div>
  <p class="abs caption" style="left:0;top:645px">Es simplemente el texto de relleno<br>de las imprentas</p>
  <p class="abs caption" style="left:195px;top:645px">Es simplemente el texto de relleno<br>de las imprentas</p>
  <p class="abs caption" style="left:390px;top:645px">Es simplemente el texto de relleno<br>de las imprentas</p>
  <p class="abs caption" style="left:585px;top:645px">Es simplemente el texto de relleno<br>de las imprentas</p>

  <div class="abs tile" style="left:0;top:683px;background:linear-gradient(180deg,#c9bfb2,#524239)" role="img" aria-label="Bedroom with built-in fireplace cabinetry"></div>
  <div class="abs tile" style="left:195px;top:683px;background:linear-gradient(180deg,#a8b3a0,#4a3426)" role="img" aria-label="Dining table by large windows"></div>
  <div class="abs tile" style="left:390px;top:683px;background:linear-gradient(180deg,#5a4f48,#3a2a20)" role="img" aria-label="Open kitchen with bar and stools"></div>
  <div class="abs tile" style="left:585px;top:683px;background:linear-gradient(180deg,#cfc8bc,#3a3430)" role="img" aria-label="Bright kitchen with island and pendant lights"></div>
  <p class="abs caption" style="left:0;top:805px">Es simplemente el texto de relleno<br>de las imprentas</p>
  <p class="abs caption" style="left:195px;top:805px">Es simplemente el texto de relleno<br>de las imprentas</p>
  <p class="abs caption" style="left:390px;top:805px">Es simplemente el texto de relleno<br>de las imprentas</p>
  <p class="abs caption" style="left:585px;top:805px">Es simplemente el texto de relleno<br>de las imprentas</p>

  <h2 class="abs section-title" style="top:868px">About Bramble Oak</h2>
  <div class="abs rule" style="top:895px;left:324px;width:126px"></div>
  <p class="abs about">Es simplemente el texto de relleno de las imprentas y archivos de texto. Lorem Ipsum ha sido el texto de relleno estándar de las industrias desde el año 1500, cuando un impresor (N. del T. persona que se dedica a la imprenta) desconocido usó una galería de textos y los mezcló de tal manera que</p>
  <div class="abs btn-solid">Click here for more info</div>

  <footer class="abs site-footer"></footer>
  <p class="abs footer-nav">Home<span>/</span>Gallery<span>/</span>Services<span>/</span>Warranty<span>/</span>Contact</p>
  <p class="abs copyright">© 2015. Bramble Oak. All rights reserved.</p>
  <div class="abs social"><i></i><i></i><i></i><i></i><i></i></div>
  <div class="abs footer-brand"><span class="brand-dot"></span>Bramble Oak</div>
</body>
</html>
```